One business card required with 2 company logos and 2 people's details

One business card required.
No preference on design - One side could show the 2 different business logos for the companies we own. The reverse could have the details shown below.
Another option could be one business one side and one business on the reverse. Happy to receive designs.

Dora Pellham
07700 913 286
Rowena Tindall
07700 958 137

website: quietmeadowbloom.co.uk
email: info@quietmeadowbloom.co.uk

website: brightharbourevents.co.uk
email: info:brightharbourevents.co.uk

May be nice to have icons instead of the words email/website?

I have included different versions of the logos to help with your design.

Contact Information for Business Card

see project overview

Requirements
Must have
• both company logos, both contact names and contact details

```html
<!DOCTYPE html>
<html lang="en">
<head>
<meta charset="utf-8">
<title>Business Card – Front and Back</title>
<link href="https://fonts.googleapis.com/css2?family=Roboto:wght@400;500;700&display=swap" rel="stylesheet">
<style>
  :root {
    --page-bg: #262626;
    --card-bg: #ffffff;
    --brand-blue: #0a7be6;
    --brand-blue-deep: #0a4fb8;
    --brand-slate: #424260;
    --brand-violet: #9a55f0;
    --brand-navy: #2e2b4f;
    --text-light: #ffffff;
  }
  * { margin: 0; padding: 0; box-sizing: border-box; }
  html, body { width: 1200px; height: 1200px; overflow: hidden; }
  body {
    background: var(--page-bg);
    font-family: 'Roboto', sans-serif;
    position: relative;
  }
  .card {
    position: absolute;
    left: 200px;
    width: 800px;
    height: 457px;
    background: var(--card-bg);
    border-radius: 26px;
    overflow: hidden;
  }
  .card--events { top: 120px; }
  .card--bloom { top: 623px; }
  .card__wave { position: absolute; inset: 0; width: 800px; height: 457px; }

  .contacts { position: absolute; color: var(--text-light); }
  .contacts--left { left: 37px; top: 240px; }
  .contacts--right { right: 50px; top: 242px; text-align: right; }
  .contact__name { font-weight: 500; font-size: 27px; line-height: 34px; letter-spacing: -0.2px; }
  .contact__line {
    font-size: 18px; line-height: 24px; letter-spacing: 0.2px;
    display: flex; align-items: center; gap: 8px;
  }
  .contacts--right .contact__line { justify-content: flex-end; }
  .contact__group { margin-bottom: 6px; }
  .contact__web { margin-top: 10px; }
  .contact__web .contact__line { line-height: 23px; }
  .icon { width: 14px; height: 14px; fill: var(--text-light); flex: none; }

  .brand {
    position: absolute;
    display: flex; flex-direction: column; align-items: center;
    font-weight: 500; text-align: center;
  }
  .brand--events { left: 470px; top: 110px; width: 240px; color: var(--brand-blue-deep); }
  .brand--bloom { left: 60px; top: 120px; width: 280px; color: var(--brand-navy); }
  .brand__mark { width: 70px; height: 70px; border-radius: 50%; margin-bottom: 18px; }
  .brand--events .brand__mark { background: var(--brand-blue); }
  .brand--bloom .brand__mark { background: var(--brand-violet); }
  .brand__name { font-size: 34px; line-height: 40px; }
</style>
</head>
<body>

<section class="card card--events" aria-label="Card front">
  <svg class="card__wave" viewBox="0 0 800 457" aria-hidden="true">
    <defs>
      <linearGradient id="eventsEdge" x1="0" y1="0" x2="1" y2="1">
        <stop offset="0" stop-color="#0a3fa8"/>
        <stop offset="1" stop-color="#1a9ad6"/>
      </linearGradient>
    </defs>
    <path d="M0,72 C150,64 235,130 325,250 C415,370 510,440 640,457 L0,457 Z" fill="url(#eventsEdge)"/>
    <path d="M0,76 C142,70 222,140 310,260 C400,380 500,444 610,457 L0,457 Z" fill="#0a7be6"/>
    <path d="M0,73 C148,66 230,134 318,255 C408,376 506,442 628,457" fill="none" stroke="#fff" stroke-width="2.5"/>
  </svg>

  <div class="contacts contacts--left">
    <div class="contact__group">
      <p class="contact__name">Rowena Tindall</p>
      <p class="contact__line"><svg class="icon" viewBox="0 0 24 24"><path d="M6.6 10.8a15.2 15.2 0 0 0 6.6 6.6l2.2-2.2a1 1 0 0 1 1-.25 11.4 11.4 0 0 0 3.6.57 1 1 0 0 1 1 1V20a1 1 0 0 1-1 1A17 17 0 0 1 3 4a1 1 0 0 1 1-1h3.5a1 1 0 0 1 1 1c0 1.25.2 2.45.57 3.57a1 1 0 0 1-.25 1z"/></svg>07700 958 137</p>
    </div>
    <div class="contact__group">
      <p class="contact__name">Dora Pellham</p>
      <p class="contact__line"><svg class="icon" viewBox="0 0 24 24"><path d="M6.6 10.8a15.2 15.2 0 0 0 6.6 6.6l2.2-2.2a1 1 0 0 1 1-.25 11.4 11.4 0 0 0 3.6.57 1 1 0 0 1 1 1V20a1 1 0 0 1-1 1A17 17 0 0 1 3 4a1 1 0 0 1 1-1h3.5a1 1 0 0 1 1 1c0 1.25.2 2.45.57 3.57a1 1 0 0 1-.25 1z"/></svg>07700 913 286</p>
    </div>
    <div class="contact__web">
      <p class="contact__line"><svg class="icon" viewBox="0 0 24 24"><path d="M2 5h20v14H2z M3 6l9 7 9-7" fill="#fff" stroke="#0a7be6" stroke-width="1.5"/></svg>info@quietmeadowbloom.co.uk</p>
      <p class="contact__line"><svg class="icon" viewBox="0 0 24 24"><circle cx="12" cy="12" r="10"/><path d="M2 12h20M12 2c3 3 3 17 0 20M12 2c-3 3-3 17 0 20" fill="none" stroke="#0a7be6" stroke-width="1.5"/></svg>quietmeadowbloom.co.uk</p>
    </div>
  </div>

  <div class="brand brand--events">
    <span class="brand__mark" aria-hidden="true"></span>
    <p class="brand__name">Bright Harbour Events</p>
  </div>
</section>

<section class="card card--bloom" aria-label="Card back">
  <svg class="card__wave" viewBox="0 0 800 457" aria-hidden="true">
    <defs>
      <linearGradient id="bloomEdge" x1="0" y1="1" x2="1" y2="0">
        <stop offset="0" stop-color="#b05cf5"/>
        <stop offset="0.55" stop-color="#3b4fd6"/>
        <stop offset="1" stop-color="#1a9ad6"/>
      </linearGradient>
    </defs>
    <path d="M180,457 C370,425 455,330 555,210 C640,110 700,78 800,76 L800,457 Z" fill="url(#bloomEdge)"/>
    <path d="M210,457 C390,428 470,335 570,215 C652,118 710,84 800,82 L800,457 Z" fill="#424260"/>
    <path d="M195,457 C380,426 462,332 562,212 C646,114 705,81 800,79" fill="none" stroke="#fff" stroke-width="2.5"/>
  </svg>

  <div class="brand brand--bloom">
    <span class="brand__mark" aria-hidden="true"></span>
    <p class="brand__name">Quiet Meadow Bloom</p>
  </div>

  <div class="contacts contacts--right">
    <div class="contact__group">
      <p class="contact__name">Rowena Tindall</p>
      <p class="contact__line">07700 958 137<svg class="icon" viewBox="0 0 24 24"><path d="M6.6 10.8a15.2 15.2 0 0 0 6.6 6.6l2.2-2.2a1 1 0 0 1 1-.25 11.4 11.4 0 0 0 3.6.57 1 1 0 0 1 1 1V20a1 1 0 0 1-1 1A17 17 0 0 1 3 4a1 1 0 0 1 1-1h3.5a1 1 0 0 1 1 1c0 1.25.2 2.45.57 3.57a1 1 0 0 1-.25 1z"/></svg></p>
    </div>
    <div class="contact__group">
      <p class="contact__name">Dora Pellham</p>
      <p class="contact__line">07700 913 286<svg class="icon" viewBox="0 0 24 24"><path d="M6.6 10.8a15.2 15.2 0 0 0 6.6 6.6l2.2-2.2a1 1 0 0 1 1-.25 11.4 11.4 0 0 0 3.6.57 1 1 0 0 1 1 1V20a1 1 0 0 1-1 1A17 17 0 0 1 3 4a1 1 0 0 1 1-1h3.5a1 1 0 0 1 1 1c0 1.25.2 2.45.57 3.57a1 1 0 0 1-.25 1z"/></svg></p>
    </div>
    <div class="contact__web">
      <p class="contact__line">info@quietmeadowbloom.co.uk<svg class="icon" viewBox="0 0 24 24"><path d="M2 5h20v14H2z M3 6l9 7 9-7" fill="#fff" stroke="#424260" stroke-width="1.5"/></svg></p>
      <p class="contact__line">quietmeadowbloom.co.uk<svg class="icon" viewBox="0 0 24 24"><circle cx="12" cy="12" r="10"/><path d="M2 12h20M12 2c3 3 3 17 0 20M12 2c-3 3-3 17 0 20" fill="none" stroke="#424260" stroke-width="1.5"/></svg></p>
    </div>
  </div>
</section>

</body>
</html>
```